Customer Value Leaflet

We need a bi-fold brochure designing, based on the attached PDF wireframes. Our company name is brambleharvik.com (of which the logo is currently being designed). The corporate colour is orange (the exact shade of which we are happy to leave to the designers discretion).

The leaflet will distributed to customer experience experts and marketers so the design needs to be bright, engaging, clean and simple. Design is critical.

It Company

```html
<!DOCTYPE html>
<html lang="en">
<head>
<meta charset="utf-8">
<title>Customer Lifetime Value – brambleharvik.com</title>
<link rel="stylesheet" href="https://fonts.googleapis.com/css2?family=Open+Sans:wght@300;400;700&display=swap">
<style>
  :root {
    --paper: #ffffff;
    --dot-tone: #f6f6f6;
    --ink: #333333;
    --brand-orange: #f9aa33;
  }
  * { margin: 0; padding: 0; box-sizing: border-box; }
  html, body {
    width: 1200px;
    height: 1200px;
    overflow: hidden;
    background: var(--paper);
  }
  .panel {
    position: relative;
    width: 1200px;
    height: 1200px;
    font-family: "Open Sans", Arial, sans-serif;
    color: var(--ink);
  }
  .panel-backdrop {
    position: absolute;
    inset: 0;
    background: var(--dot-tone);
  }
  .headline {
    position: absolute;
    left: 117px;
    top: 219px;
    width: 1000px;
    font-size: 60px;
    font-weight: 300;
    line-height: 78px;
    letter-spacing: -0.3px;
  }
  .headline-highlight {
    color: var(--brand-orange);
    text-decoration: underline;
    text-decoration-thickness: 2px;
    text-underline-offset: 6px;
  }
  .payoff {
    position: absolute;
    right: 107px;
    top: 544px;
    width: 1000px;
    text-align: right;
    font-size: 60px;
    font-weight: 300;
    line-height: 78px;
    letter-spacing: -0.3px;
  }
  .footer-cta {
    position: absolute;
    left: 0;
    right: 0;
    top: 990px;
    text-align: center;
    font-size: 33px;
    font-weight: 400;
    line-height: 44px;
    padding-right: 10px;
  }
  .footer-cta strong { font-weight: 700; }
</style>
</head>
<body>
  <main class="panel">
    <div class="panel-backdrop" role="img" aria-label="Light grey dotted grid pattern covering the background"></div>

    <h1 class="headline">By predicting <span class="headline-highlight">Customer Lifetime<br>Value</span> today</h1>

    <p class="payoff">...you can optimise<br>your business for tomorrow</p>

    <p class="footer-cta">Find our more at <strong>www.brambleharvik.com</strong></p>
  </main>
</body>
</html>
```